VORTAL MED -DIAGNOSTIC CENTRE FOR IMAGES

Our Activity provides diagnostic services for images (RMI, Tac, RX, Ultrasound etc.)
We would like to create a broschure that illustrates our services.
We would like to give maximum attention to the Diagnostic service dedicated to "HEART", therefore maximum evidence to the world of Cardiology.
In the background we would like to highlight the other diagnostic services dedicated to the Rest of the Body (Brain, Knees Legs etc.)
Target Market(s)
PERSONS WHO NEED TO PERFORM DIAGNOSTIC TESTS (MRI, CT, ULTRASOUND, RX ETC.)
Industry/Entity Type
HEALTH
Requirements
Must have
- The company logo, must have diagnostic images (MRI, CT, X-ray, ultrasound), must be simple and intuitive, which is harmonious with the colors of our company logo
Should not have
- Colours that are not in harmony with our company logo

```html
<!DOCTYPE html>
<html lang="en">
<head>
<meta charset="utf-8">
<title>Vortal Med – Diagnostic Brochure</title>
<link href="https://fonts.googleapis.com/css2?family=Inter:wght@400;500;600;700;800&display=swap" rel="stylesheet">
<style>
:root{
  --teal:#00ada0;
  --blue:#1f74c6;
  --navy:#0d2d55;
  --sky:#e6f5fd;
  --ink:#1b1b1b;
  --grey:#3f4448;
  --paper:#ffffff;
}
*{margin:0;padding:0;box-sizing:border-box}
html,body{width:1200px;height:848px;overflow:hidden;background:var(--paper)}
body{font-family:"Inter",sans-serif;color:var(--ink)}
.brochure{position:relative;width:1200px;height:848px;overflow:hidden;background:var(--paper)}
.abs{position:absolute}
.sky{background:var(--sky)}
.outline-box{border:2px solid var(--navy);border-radius:12px}
.ring{border:4px solid var(--teal);border-radius:50%}
.bar-teal{background:var(--teal);border-radius:6px}

.photo{left:58px;top:112px;width:492px;height:328px;border-radius:22px;
  background:linear-gradient(135deg,#eef1f4 0%,#d9dee3 45%,#c9d2da 65%,#8fc3ec 85%,#6fb1e6 100%)}
.brand{font-family:"Inter",sans-serif;font-weight:700;color:var(--blue);letter-spacing:-0.5px;white-space:nowrap;line-height:1}
.brand-photo{left:0;width:608px;top:250px;text-align:center;font-size:42px}
.brand-top{left:808px;top:90px;font-size:31px}
.brand-bottom{left:436px;top:790px;font-size:21px}

.service{position:absolute;width:140px;text-align:center}
.tile{width:69px;height:69px;margin:0 auto;background:var(--teal);border-radius:8px;display:flex;align-items:center;justify-content:center}
.tile svg{width:34px;height:34px;fill:none;stroke:#fff;stroke-width:2;stroke-linecap:round;stroke-linejoin:round}
.service-label{margin-top:6px;font-size:14.5px;font-weight:700;line-height:16.5px;color:var(--ink)}

.dots{left:524px;top:564px}

.contact-head{left:31px;top:671px;font-size:19px;font-weight:800;color:var(--navy);letter-spacing:-0.2px}
.contact-cta{left:31px;top:700px;font-size:20px;font-weight:800;color:var(--teal);letter-spacing:-0.2px}
.contact-lines{left:38px;top:736px;font-size:14px;line-height:19.5px;color:var(--navy)}
.contact-phone{left:38px;top:795px;font-size:14px;color:var(--navy)}

.triangles{left:641px;top:255px}

.headline{left:720px;width:366px;text-align:center}
.headline-top{top:174px;font-size:39px;font-weight:500;color:var(--blue);letter-spacing:0.3px;line-height:1}
.headline-main{top:212px;font-size:55px;font-weight:800;color:var(--teal);letter-spacing:0.5px;line-height:1}
.headline-sub{left:700px;width:406px;top:271px;font-size:17px;color:var(--grey);text-align:center}

.portrait{left:747px;top:378px;width:304px;height:304px;border-radius:50%;
  background:radial-gradient(circle at 50% 45%,#f4f6f7 0%,#e1e6e8 45%,#1fb3a6 72%,var(--teal) 100%)}
.accent-square{left:1109px;top:409px;width:71px;height:70px;border-radius:9px;background:var(--teal)}

.pill{position:absolute;height:26px;border-radius:6px;background:var(--blue);color:#fff;font-size:14px;font-weight:500;display:flex;align-items:center;justify-content:center;white-space:nowrap}
</style>
</head>
<body>
<main class="brochure">

  <!-- left panel decoration -->
  <div class="abs sky" style="left:0;top:0;width:134px;height:172px"></div>
  <div class="abs outline-box" style="left:81px;top:-14px;width:110px;height:53px;border-top:none;border-radius:0 0 12px 12px"></div>
  <div class="abs bar-teal" style="left:38px;top:78px;width:210px;height:12px"></div>
  <div class="abs ring" style="left:463px;top:49px;width:29px;height:29px"></div>

  <div class="abs photo" role="img" aria-label="Photograph of an MRI scanner room with patient table"></div>
  <div class="abs brand brand-photo">VORTAL MED</div>

  <!-- services -->
  <div class="service" style="left:76px;top:395px">
    <div class="tile"><svg viewBox="0 0 34 34"><path d="M17 28 C7 21 4 16 4 11.5 A6.5 6.5 0 0 1 17 9 A6.5 6.5 0 0 1 30 11.5 C30 16 27 21 17 28Z"/><path d="M6 17h6l2-4 3 7 2-4h9"/></svg></div>
    <div class="service-label">Cardiology<br>Services</div>
  </div>
  <div class="service" style="left:238px;top:395px">
    <div class="tile"><svg viewBox="0 0 34 34"><path d="M12 27c-4 0-7-3-7-7 0-2 1-3 1-5-1-4 2-8 6-8 1-2 3-3 5-3s4 1 5 3c4 0 7 4 6 8 0 2 1 3 1 5 0 4-3 7-7 7"/><path d="M17 4v24M12 12c2 0 3 2 3 4M22 12c-2 0-3 2-3 4M9 20c2 0 4-1 5-3M25 20c-2 0-4-1-5-3"/></svg></div>
    <div class="service-label">Neurology<br>Scans</div>
  </div>
  <div class="service" style="left:396px;top:395px">
    <div class="tile"><svg viewBox="0 0 34 34"><path d="M8 5H5v24h3M26 5h3v24h-3"/><circle cx="17" cy="9" r="2.5"/><path d="M13 14h8l-1 8h-2v6h-2v-6h-2z"/></svg></div>
    <div class="service-label">Full-body<br>Scans</div>
  </div>
  <div class="service" style="left:158px;top:511px">
    <div class="tile"><svg viewBox="0 0 34 34"><rect x="4" y="4" width="26" height="26" rx="3"/><path d="M13 8v4c0 2 2 3 4 3s4-1 4-3V8M13 26v-3c0-2 2-3 4-3s4 1 4 3v3M14 16h6"/></svg></div>
    <div class="service-label">Orthopedic<br>Scans</div>
  </div>
  <div class="service" style="left:318px;top:511px">
    <div class="tile"><svg viewBox="0 0 34 34"><circle cx="17" cy="9" r="4.5"/><path d="M5 24c2-5 6-8 12-8s10 3 12 8"/><path d="M10 22l4 5 9-9"/></svg></div>
    <div class="service-label">Customized<br>Care</div>
  </div>

  <svg class="abs dots" width="56" height="56" viewBox="0 0 56 56" aria-hidden="true">
    <g fill="var(--navy)">
      <circle cx="3" cy="3" r="2.2"/><circle cx="19" cy="3" r="2.2"/><circle cx="35" cy="3" r="2.2"/><circle cx="51" cy="3" r="2.2"/>
      <circle cx="3" cy="19" r="2.2"/><circle cx="19" cy="19" r="2.2"/><circle cx="35" cy="19" r="2.2"/><circle cx="51" cy="19" r="2.2"/>
      <circle cx="3" cy="35" r="2.2"/><circle cx="19" cy="35" r="2.2"/><circle cx="35" cy="35" r="2.2"/><circle cx="51" cy="35" r="2.2"/>
      <circle cx="3" cy="51" r="2.2"/><circle cx="19" cy="51" r="2.2"/><circle cx="35" cy="51" r="2.2"/><circle cx="51" cy="51" r="2.2"/>
    </g>
  </svg>

  <div class="abs sky" style="left:28px;top:490px;width:27px;height:95px;border-radius:6px"></div>
  <div class="abs sky" style="left:0;top:524px;width:89px;height:27px;border-radius:0 6px 6px 0"></div>

  <!-- contact -->
  <div class="abs contact-head">FOR APPOINTMENTS AND INQUIRIES</div>
  <div class="abs contact-cta">CONTACT US TODAY!</div>
  <div class="abs contact-lines">Addressline 1<br>Addressline 2</div>
  <div class="abs contact-phone">Phone no: +12 3456 789</div>
  <div class="abs outline-box" style="left:245px;top:810px;width:110px;height:60px;border-bottom:none;border-radius:12px 12px 0 0"></div>

  <div class="abs ring" style="left:586px;top:654px;width:30px;height:30px"></div>
  <div class="abs sky" style="left:499px;top:747px;width:203px;height:110px;border-radius:18px 18px 0 0"></div>
  <div class="abs brand brand-bottom">VORTAL MED</div>
  <div class="abs bar-teal" style="left:614px;top:815px;width:210px;height:5px"></div>

  <!-- right panel -->
  <div class="abs sky" style="left:696px;top:0;width:36px;height:119px;border-radius:0 0 8px 8px"></div>
  <div class="abs sky" style="left:649px;top:36px;width:129px;height:36px;border-radius:8px"></div>
  <div class="abs" style="left:990px;top:32px;width:220px;height:12px;border-radius:6px;background:var(--navy)"></div>
  <div class="abs sky" style="left:1136px;top:93px;width:80px;height:202px;border-radius:18px 0 0 18px"></div>
  <div class="abs outline-box" style="left:1159px;top:240px;width:60px;height:109px;border-right:none;border-radius:12px 0 0 12px"></div>

  <div class="abs brand brand-top">VORTAL MED</div>

  <svg class="abs triangles" width="22" height="75" viewBox="0 0 22 75" aria-hidden="true">
    <g fill="var(--teal)">
      <path d="M11 0L21 12H1z"/><path d="M11 21L21 33H1z"/><path d="M11 41L21 53H1z"/><path d="M11 62L21 74H1z"/>
    </g>
  </svg>

  <div class="abs headline headline-top">YOUR HEART</div>
  <div class="abs headline headline-main">MATTERS</div>
  <div class="abs headline-sub">Diagnostic Services for a Healthier You</div>

  <div class="abs portrait" role="img" aria-label="Photograph of a smiling doctor in a white coat holding a red heart, set in a teal circle"></div>
  <div class="abs accent-square"></div>

  <div class="pill" style="left:663px;top:717px;width:190px">Highly Experienced Staff</div>
  <div class="pill" style="left:913px;top:717px;width:221px">Knowledgeable Support Staff</div>
  <div class="pill" style="left:675px;top:760px;width:166px">Friendly Environment</div>
  <div class="pill" style="left:936px;top:760px;width:175px">Cutting-edge Systems</div>

</main>
</body>
</html>
```